Card design for orthopaedic surgeons working as The Brightwater Joint Centre

Business cards, letterhead

Colors

Designer to choose colors to be used in the design.

Requirements
Must have
• Late addition.
• Cards letterhead must have logos of
• Crestmoor Lindell College of Surgeons
• Varenwood Bone Health Association
Nice to have
• Back of card to have space for appointment time to be added by hand and some blank space for writing incidental other notes.

```html
<!DOCTYPE html>
<html lang="en">
<head>
<meta charset="utf-8">
<title>The Brightwater Joint Centre – Business Cards</title>
<link href="https://fonts.googleapis.com/css2?family=Roboto:wght@300;400;500;700&display=swap" rel="stylesheet">
<style>
  :root {
    --backdrop: #7d7d7d;
    --card: #ffffff;
    --navy: #0f2f4d;
    --deep-navy: #062c47;
    --sky: #4aa3e0;
    --ink: #1d2b3a;
    --rule: #6aa9d6;
  }
  * { box-sizing: border-box; margin: 0; padding: 0; }
  html, body { width: 1200px; height: 675px; overflow: hidden; }
  body {
    background: var(--backdrop);
    font-family: "Roboto", Arial, sans-serif;
    color: var(--ink);
    display: flex;
    align-items: center;
    justify-content: center;
    gap: 40px;
  }
  .card {
    position: relative;
    width: 525px;
    height: 300px;
    background: var(--card);
    border-radius: 16px;
    overflow: hidden;
    box-shadow: 0 8px 18px rgba(0,0,0,0.35);
  }
  .brand-name {
    font-weight: 300;
    color: var(--sky);
    white-space: nowrap;
    letter-spacing: -0.3px;
  }

  /* Appointment side */
  .appointment .brand-name {
    position: absolute;
    top: 34px;
    right: 48px;
    font-size: 22px;
  }
  .appointment-title {
    position: absolute;
    top: 100px;
    left: 40px;
    font-size: 21px;
    font-weight: 700;
    color: var(--navy);
  }
  .appointment-title .lead { color: var(--sky); font-weight: 500; }
  .field-row {
    position: absolute;
    left: 40px;
    right: 40px;
    display: flex;
    align-items: flex-end;
    gap: 8px;
    font-size: 14px;
    font-weight: 400;
  }
  .field-row.name { top: 146px; }
  .field-row.time { top: 176px; }
  .fill-line {
    flex: 1;
    border-bottom: 1.5px dotted #333;
    height: 12px;
  }
  .fill-line.short { flex: 0 0 150px; }
  .tick {
    display: inline-flex;
    align-items: center;
    gap: 4px;
    font-size: 12.5px;
    font-weight: 300;
  }
  .tick::before {
    content: "";
    width: 10px;
    height: 10px;
    border: 1.5px solid #222;
  }
  .day-row {
    position: absolute;
    top: 214px;
    left: 40px;
    right: 40px;
    display: flex;
    justify-content: space-between;
  }
  .notice {
    position: absolute;
    left: 40px;
    right: 30px;
    bottom: 28px;
    font-size: 13px;
    color: var(--navy);
  }

  /* Contact side */
  .contact .brand-name {
    position: absolute;
    top: 138px;
    left: 30px;
    font-size: 20px;
  }
  .divider {
    position: absolute;
    left: 298px;
    top: 46px;
    height: 150px;
    border-left: 1.2px solid var(--rule);
  }
  .person {
    position: absolute;
    left: 314px;
    top: 44px;
  }
  .person-name { font-size: 17px; font-weight: 700; color: var(--sky); }
  .person-role { font-size: 12px; font-weight: 700; color: var(--navy); margin-top: 2px; }
  .address { font-size: 11px; margin-top: 12px; line-height: 1.35; }
  .contact-list { list-style: none; margin-top: 10px; font-size: 11px; line-height: 1.55; }
  .contact-list li { display: flex; align-items: center; gap: 6px; }
  .contact-list svg { width: 10px; height: 10px; flex: none; }
  .wave { position: absolute; left: 0; bottom: 0; width: 525px; height: 110px; }
</style>
</head>
<body>

<section class="card appointment">
  <div class="brand-name">The Brightwater Joint Centre</div>
  <h2 class="appointment-title"><span class="lead">Next</span> Appointment</h2>

  <div class="field-row name"><span>Name:</span><span class="fill-line"></span></div>
  <div class="field-row time">
    <span>Time:</span><span class="fill-line short"></span>
    <span class="tick">AM</span><span class="tick">PM</span>
    <span>Date:</span><span class="fill-line"></span>
  </div>

  <div class="day-row">
    <span class="tick">MON</span><span class="tick">TUES</span><span class="tick">WED</span>
    <span class="tick">THUR</span><span class="tick">FRI</span><span class="tick">SAT</span>
  </div>

  <p class="notice">If you are unable to keep your appointment, please call us as soon as possible</p>
</section>

<section class="card contact">
  <div class="brand-name">The Brightwater Joint Centre</div>
  <div class="divider"></div>

  <div class="person">
    <div class="person-name">Daniel Harwick</div>
    <div class="person-role">President</div>
    <p class="address">48 Larkspur Valley Road<br>Suite 310, Fernhill, MI 40912</p>
    <ul class="contact-list">
      <li>
        <svg viewBox="0 0 10 10"><path d="M2 0.5 L4 2.8 L3 4 Q4.5 6 6 7 L7.2 6 L9.5 8 L8 9.6 Q3.5 9 0.4 2 Z" fill="var(--sky)"/></svg>
        555 014 2288
      </li>
      <li>
        <svg viewBox="0 0 10 10"><rect x="0.5" y="2" width="9" height="6.5" fill="var(--sky)"/><path d="M0.5 2 L5 6 L9.5 2" stroke="#fff" fill="none" stroke-width="0.9"/></svg>
        info@brightwaterjoint.com
      </li>
      <li>
        <svg viewBox="0 0 10 10"><circle cx="5" cy="5" r="4.3" fill="none" stroke="var(--sky)" stroke-width="1"/><path d="M0.7 5 H9.3 M5 0.7 Q2 5 5 9.3 M5 0.7 Q8 5 5 9.3" stroke="var(--sky)" fill="none" stroke-width="0.8"/></svg>
        www.brightwaterjoint.com
      </li>
    </ul>
  </div>

  <svg class="wave" viewBox="0 0 525 110" preserveAspectRatio="none" aria-hidden="true">
    <path d="M0 110 L0 92 C150 86 270 78 370 36 C425 14 470 4 525 2 L525 110 Z" fill="var(--sky)"/>
    <path d="M0 110 L0 97 C155 92 275 84 378 44 C430 22 472 12 525 10 L525 110 Z" fill="var(--deep-navy)"/>
  </svg>
</section>

</body>
</html>
```